Coastline Premier Retreats Business Card Design

Design a business card for Coastline Premier Retreats. Look at the website for colors and reference. Card should have logo, name, title, office number, mobile number, email, URL and a tagline like, "Luxury Hotel & Resort Email Marketing" (This might change).

https://www.coastlinepremierretreats.example

The rest I will leave up to your imagination.

Contact Information for Business Card

Logo, name, title, office number, mobile number, email, URL and a tagline like, "Luxury Hotel & Resort Email Marketing" (This might change).

```html
<!DOCTYPE html>
<html lang="en">
<head>
<meta charset="utf-8">
<title>Coastline Premier Retreats — Business Card</title>
<link href="https://fonts.googleapis.com/css2?family=Montserrat:ital,wght@0,400;0,500;0,700;1,400&display=swap" rel="stylesheet">
<style>
  :root {
    --bg: #2a2a2a;
    --card: #1b1b1b;
    --orange: #f07c16;
    --white: #ffffff;
  }
  * { box-sizing: border-box; margin: 0; padding: 0; }
  html, body { width: 1200px; height: 900px; overflow: hidden; }
  body {
    background: var(--bg);
    font-family: "Montserrat", Arial, sans-serif;
    display: flex;
    flex-direction: column;
    align-items: center;
    justify-content: center;
    gap: 40px;
  }
  .card {
    position: relative;
    width: 640px;
    height: 366px;
    background: var(--card);
    box-shadow: 0 10px 30px rgba(0,0,0,.45);
  }
  .frame {
    position: absolute;
    inset: 26px;
    border: 2px solid var(--orange);
    border-bottom: none;
  }
  .frame-foot {
    position: absolute;
    left: -2px; right: -2px; bottom: -1px;
    display: flex;
    align-items: center;
    gap: 10px;
    transform: translateY(50%);
  }
  .frame-line { height: 2px; background: var(--orange); }
  .frame-line.lead { width: 70px; }
  .frame-line.fill { flex: 1; }
  .frame-foot .tagline {
    color: var(--orange);
    font-style: italic;
    font-size: 17px;
    white-space: nowrap;
  }
  .frame-foot .address {
    color: var(--white);
    font-size: 13px;
    white-space: nowrap;
  }
  .brand {
    display: flex;
    align-items: center;
    gap: 12px;
    color: var(--white);
    font-weight: 700;
    text-transform: uppercase;
    letter-spacing: .04em;
  }
  .brand-mark { background: var(--orange); flex: none; }

  /* back */
  .card-back .brand {
    position: absolute;
    left: 50%; top: 44%;
    transform: translate(-50%, -50%);
    font-size: 26px;
    white-space: nowrap;
  }
  .card-back .brand-mark { width: 20px; height: 20px; }

  /* front */
  .card-front .brand {
    position: absolute;
    left: 56px; top: 112px;
    font-size: 17px;
    width: 215px;
    line-height: 1.25;
  }
  .card-front .brand-mark { width: 14px; height: 14px; }
  .divider {
    position: absolute;
    left: 288px; top: 86px;
    width: 1px; height: 150px;
    background: var(--orange);
  }
  .person { position: absolute; left: 308px; top: 88px; }
  .person-name {
    color: var(--orange);
    font-weight: 700;
    font-size: 24px;
    letter-spacing: .03em;
    text-transform: uppercase;
  }
  .person-title { color: var(--white); font-size: 13px; margin-top: 2px; }
  .contacts { list-style: none; margin-top: 16px; }
  .contacts li {
    display: flex; align-items: center; gap: 8px;
    color: var(--white); font-size: 12px; line-height: 22px;
    white-space: nowrap;
  }
  .contacts svg { width: 12px; height: 12px; flex: none; fill: var(--orange); }
  .contacts .accent { color: var(--orange); }
</style>
</head>
<body>

  <section class="card card-back" aria-label="Card back">
    <div class="brand"><span class="brand-mark"></span>Coastline Premier Retreats</div>
    <div class="frame">
      <div class="frame-foot">
        <span class="frame-line lead"></span>
        <span class="tagline">Luxury Hotel &amp; Resort Email Marketing</span>
        <span class="frame-line fill"></span>
      </div>
    </div>
  </section>

  <section class="card card-front" aria-label="Card front">
    <div class="frame">
      <div class="frame-foot">
        <span class="frame-line lead"></span>
        <span class="address">Po Box, 48 Harbor Lane Bayview, CA 90000</span>
        <span class="frame-line fill"></span>
      </div>
    </div>
    <div class="brand"><span class="brand-mark"></span><span class="brand-name">Coastline Premier Retreats</span></div>
    <span class="divider"></span>
    <div class="person">
      <h1 class="person-name">Daniel Reyes</h1>
      <p class="person-title">CEO/Founder</p>
      <ul class="contacts">
        <li><svg viewBox="0 0 12 12"><path d="M3 0h6a1 1 0 0 1 1 1v10a1 1 0 0 1-1 1H3a1 1 0 0 1-1-1V1a1 1 0 0 1 1-1zm0 1.5v8h6v-8z"/></svg><span class="contact-text">555.014.2200</span></li>
        <li><svg viewBox="0 0 12 12"><path d="M2.5 1l2 2.3-1 1.3a7 7 0 0 0 3.9 3.9l1.3-1 2.3 2-1.3 1.5C5 10.8 1.2 7 .9 2.3z"/></svg><span class="contact-text">+34 600 555 014</span></li>
        <li><svg viewBox="0 0 12 12"><path d="M0 2h12v8H0zm1 1v.3l5 3.2 5-3.2V3z"/></svg><span class="contact-text">info@coastlinepremierretreats.example</span></li>
        <li><svg viewBox="0 0 12 12"><path d="M6 0a6 6 0 1 0 0 12A6 6 0 0 0 6 0zm0 1.2c.8 0 1.6 1.8 1.8 4.2H4.2C4.4 3 5.2 1.2 6 1.2zM4.2 6.6h3.6C7.6 9 6.8 10.8 6 10.8S4.4 9 4.2 6.6z"/></svg><span class="contact-text">www.<span class="accent">coastlinepremierretreats</span>.example</span></li>
      </ul>
    </div>
  </section>

</body>
</html>
```